Kestrel Facilities Business Card Design

We would now like to design business cards with the new Kestrel Facilities logo

Target Market(s)

Professional

Industry/Entity Type

Professional services

Contact Information for Business Card

Employee name, title, phone number, email address, corporate office address and logo.

Font styles to use
Sans Serif

Colors
0054AA
0677BA
7BADD7
CADEEF
E8F1F8

Requirements
Must have
• My logo
Should not have
• any other pictures or images besides my logo

```html
<!DOCTYPE html>
<html lang="en">
<head>
<meta charset="utf-8">
<title>Kestrel Facilities Business Card</title>
<link href="https://fonts.googleapis.com/css2?family=Montserrat:wght@400;500;700&display=swap" rel="stylesheet">
<style>
  :root {
    --brand-blue: #3878be;
    --ink: #1a1a1a;
    --card: #ffffff;
    --backdrop: #e9ebee;
  }
  * { box-sizing: border-box; margin: 0; padding: 0; }
  html, body {
    width: 1160px; height: 1200px; overflow: hidden;
    background: var(--backdrop);
    font-family: "Montserrat", Arial, sans-serif;
  }
  .canvas { position: relative; width: 1160px; height: 1200px; }
  .card {
    position: absolute; left: 191px; width: 778px; height: 441px;
    background: var(--card);
  }
  .card--front { top: 105px; }
  .card--back { top: 654px; }

  .brand {
    position: absolute; left: 0; right: 0;
    display: flex; align-items: center; justify-content: center; gap: 14px;
    color: var(--brand-blue); font-weight: 700; letter-spacing: 0.5px;
  }
  .brand__mark { background: var(--brand-blue); flex: none; }
  .card--front .brand { top: 92px; font-size: 34px; }
  .card--front .brand__mark { width: 30px; height: 30px; }
  .card--back .brand { top: 188px; font-size: 50px; gap: 20px; }
  .card--back .brand__mark { width: 44px; height: 44px; }

  .person {
    position: absolute; right: 413px; top: 242px; text-align: right;
  }
  .person__name {
    color: var(--brand-blue); font-weight: 700; font-size: 29px; line-height: 1; letter-spacing: 0.3px;
  }
  .person__title {
    color: var(--ink); font-weight: 400; font-size: 20px; margin-top: 9px;
  }
  .divider {
    position: absolute; left: 395px; top: 233px; width: 2px; height: 83px;
    background: var(--brand-blue);
  }
  .contacts {
    position: absolute; left: 416px; top: 232px; list-style: none;
  }
  .contacts__item {
    display: flex; align-items: center; gap: 7px;
    height: 29.5px; font-size: 20px; color: var(--ink);
  }
  .contacts__icon { width: 20px; height: 20px; fill: var(--brand-blue); flex: none; }
  .address-band {
    position: absolute; left: 0; right: 0; top: 358px; height: 56px;
    background: var(--brand-blue); color: #fff;
    display: flex; align-items: center; justify-content: center;
    font-size: 20px; font-weight: 400;
  }
</style>
</head>
<body>
<div class="canvas">
  <section class="card card--front">
    <div class="brand"><span class="brand__mark"></span><span class="brand__name">Kestrel Facilities</span></div>

    <div class="person">
      <p class="person__name">DANA WHITLOCK</p>
      <p class="person__title">Co-Founder</p>
    </div>
    <div class="divider"></div>
    <ul class="contacts">
      <li class="contacts__item">
        <svg class="contacts__icon" viewBox="0 0 20 20" aria-hidden="true"><path d="M2 7c0-2 3-3 8-3s8 1 8 3v1.5h-4V7H6v1.5H2z"/><rect x="4" y="9" width="12" height="8" rx="1"/></svg>
        <span>+254-100-55512</span>
      </li>
      <li class="contacts__item">
        <svg class="contacts__icon" viewBox="0 0 20 20" aria-hidden="true"><path d="M1 5h18v1.5l-9 5.5-9-5.5z"/><path d="M1 8.5l9 5.5 9-5.5V16H1z"/></svg>
        <span>info@kestrelfacilities.com</span>
      </li>
      <li class="contacts__item">
        <svg class="contacts__icon" viewBox="0 0 20 20" aria-hidden="true"><circle cx="10" cy="10" r="9"/><path d="M5 5c2 0 3 1 3 3s-2 2-2 4-2 1-3 0c-1-2-1-5 2-7zM12 12c2-1 4 0 4 1s-2 4-4 4-1-4 0-5z" fill="#fff"/></svg>
        <span>www.kestrelfacilities.com</span>
      </li>
    </ul>

    <div class="address-band">1480 N. Harbor Lane Suite 210 Crestvale.14</div>
  </section>

  <section class="card card--back">
    <div class="brand"><span class="brand__mark"></span><span class="brand__name">Kestrel Facilities</span></div>
  </section>
</div>
</body>
</html>
```